Packaging design - PROTEIN BALLS

PACKAGING
The packaging is a round carton roll, size: Ø73x180 mm, mockup sample enclosed, The label on the carton roll should have a size of 225x178 mm (width x height)

PRODUCT
Chrunchy, cheesy PROTEIN BALLS (100% pure cheese) with a huge amount of protein (65%), a lot of calcium and very low carbogydrates (3%). Diameter about 1.5 cm.

DESIGN
Since our customers are very sporty people, runner, bodybuilder, etc. The design must fit to this sporty customer segment.

FILES
We need the open data for InDesign with all fonts and pictures. If there are licenses tu buy, we will do it.

SUMMARY
1. SNACK
• Crunchy cheese balls with a diameter of about 1.5cm
• 3 different flavors: "Swiss Alpine Salt", "Provencale" and "Hot Chili"
• High in Protein (65%) and Calcium (2%)
• Low in carbohydrates (3%)

2. PACKAGING
• Carton roll, size: Ø73x180 mm
• Background can be every color, but we think a black one will be high premium.
• Maybe different sports are represented in the background, maybe also cheese
• Be creative
• Label applied, size: 225x178 mm

3. DESIGN
• Product name = (Cheese) PROTEIN BALLS
• 3 different colors for the 3 flavors "Swiss Alpine Salt", "Provencale" and "Hot Chili"
• HighProtein, High Calcium and LowCarb must be pointed out on the front
• Swissness: Swiss made must be pointed out
• fresh and young design, most customers are sporty people, pumper with a strong body awareness

Target Market(s)

TARGET CUSTOMER
Our main customers are extremely sporty people, who work very hard on their muscles and fitness, most of them are runners, cross fitnesser, bodybuilders, etc We will launch the product in fitness centers, in supplement shops and we are planning to make some stories with sporty influencer.

Font styles to use
Serif
Sans Serif

Requirements
Must have
• Cheese, naturalness, healthy, PROTEIN balls, muscles, Swissness must showed on the product.

```html
<!DOCTYPE html>
<html lang="en">
<head>
<meta charset="utf-8">
<title>Cheese Protein Balls – Label</title>
<link href="https://fonts.googleapis.com/css2?family=Oswald:wght@400;600;700&family=Kaushan+Script&family=Roboto+Condensed:wght@400;700&display=swap" rel="stylesheet">
<style>
  :root{
    --bg:#f2f2f2;
    --black:#0b0b0b;
    --glow:#c9848a;
    --glow-soft:rgba(201,132,138,.0);
    --yellow:#f3c21b;
    --gold:#e9b84a;
    --red:#d3212c;
    --white:#ffffff;
    --ink:#1a1a1a;
    --grey:#bdbdbd;
  }
  *{box-sizing:border-box;margin:0;padding:0}
  html,body{width:900px;height:1200px;overflow:hidden;background:var(--bg)}
  .label{
    position:absolute;left:20px;top:260px;width:860px;height:680px;
    background:
      radial-gradient(ellipse 300px 200px at 50% 40%, rgba(214,140,150,.75), var(--glow-soft) 80%),
      linear-gradient(180deg,#151515 0%,#3a2a2c 45%,#151515 100%);
    background-color:var(--black);
    overflow:hidden;font-family:"Roboto Condensed",Arial,sans-serif;color:var(--white);
  }
  .streaks{position:absolute;inset:0}
  /* left column */
  .claim{position:absolute;left:22px;top:18px;font-family:"Oswald",sans-serif;font-weight:700;
    color:var(--yellow);font-size:50px;line-height:.95;text-transform:uppercase}
  .swiss{position:absolute;left:28px;top:200px;display:flex;align-items:center;gap:10px}
  .swiss-dot{width:62px;height:62px;border-radius:50%;background:var(--red);border:3px solid var(--white)}
  .swiss-text{font-family:"Oswald",sans-serif;font-weight:700;font-size:22px;line-height:1;color:var(--white)}
  .info-box{position:absolute;left:22px;top:340px;width:128px;height:180px;background:var(--white);
    color:var(--ink);font-size:10px;line-height:1.7;padding:10px 8px}
  .info-box p{border-bottom:1px solid #ccc}
  /* centre */
  .title{position:absolute;left:190px;right:190px;top:14px;text-align:center;font-family:"Oswald",sans-serif;
    font-weight:700;font-style:italic;text-transform:uppercase}
  .title .cheese{display:block;color:var(--yellow);font-size:64px;line-height:1}
  .title .product{display:block;color:var(--white);font-size:62px;line-height:.95;letter-spacing:1px}
  .athletes{position:absolute;left:300px;top:190px;width:260px;height:230px;
    background:radial-gradient(ellipse at 50% 55%,rgba(255,255,255,.85),rgba(255,255,255,.25) 60%,transparent 75%)}
  .tagline{position:absolute;left:210px;top:440px;font-family:"Kaushan Script",cursive;color:var(--yellow);
    font-size:38px;line-height:1.05;transform:rotate(-8deg)}
  .snack{position:absolute;left:330px;top:420px;width:330px;height:190px;border-radius:50% 50% 40% 40%;
    background:radial-gradient(ellipse at 40% 50%,#f4e6b0,#e3c77a 55%,rgba(227,199,122,0) 75%)}
  .flavour{position:absolute;left:230px;right:230px;bottom:30px;height:34px;background:var(--black);
    border:1px solid var(--grey);text-align:center;font-family:"Oswald",sans-serif;font-size:22px;
    letter-spacing:3px;line-height:32px;color:var(--white)}
  /* right column */
  .badges{position:absolute;right:24px;top:14px;display:flex;gap:10px}
  .badge{width:66px;height:66px;border-radius:50%;background:var(--red);border:3px solid var(--white)}
  .lowcarb{position:absolute;right:22px;top:92px;width:178px;background:var(--white);color:var(--red);
    font-weight:700;font-size:16px;text-align:center;padding:4px 0}
  .nutrition{position:absolute;right:22px;top:126px;width:178px;background:var(--white);color:var(--ink);
    padding:6px 8px;font-size:9.5px}
  .nutrition h2{font-family:"Oswald",sans-serif;font-size:17px;line-height:1.1;border-bottom:4px solid var(--ink)}
  .nutrition table{width:100%;border-collapse:collapse}
  .nutrition td{border-bottom:1px solid #999;padding:2px 0}
  .nutrition td:last-child{text-align:right;font-weight:700}
  .storage{position:absolute;right:22px;top:428px;width:178px;text-align:center;font-size:14px}
  .maker{position:absolute;right:22px;top:470px;width:178px;font-size:10.5px;line-height:1.55;color:var(--white)}
  .web{position:absolute;right:22px;top:600px;width:178px;display:flex;align-items:center;gap:5px;font-size:10.5px}
  .web i{width:12px;height:12px;border-radius:50%;background:var(--white);display:inline-block}
</style>
</head>
<body>
<main class="label">
  <svg class="streaks" width="860" height="680" viewBox="0 0 860 680" aria-hidden="true">
    <g stroke="#e9b84a" stroke-width="1.5" opacity=".6" fill="none">
      <path d="M180 120 L700 60"/><path d="M170 150 L720 95"/><path d="M200 330 L700 280"/>
    </g>
  </svg>

  <div class="claim">100 %<br>Pure<br>Cheese</div>
  <div class="swiss"><span class="swiss-dot"></span><span class="swiss-text">SWISS<br>MADE</span></div>
  <div class="info-box">
    <p>Ingredients: cheese</p><p>Net weight: 60 g</p><p>Best before:</p><p>Lot number:</p><p>Made in Switzerland</p>
  </div>

  <h1 class="title"><span class="cheese">Cheese</span><span class="product">Protein<br>Balls</span></h1>
  <div class="athletes" role="img" aria-label="Silhouettes of athletes: bodybuilder, runner and gymnast in front of a light glow"></div>
  <div class="snack" role="img" aria-label="Pile of crunchy golden cheese protein balls with alpine salt"></div>
  <p class="tagline">Crunchy<br>&nbsp;&nbsp;Cheesy</p>
  <div class="flavour">SWISS ALPINE SALT</div>

  <div class="badges"><span class="badge"></span><span class="badge"></span></div>
  <div class="lowcarb">Low in carbohydrates</div>
  <section class="nutrition">
    <h2>Nutrition Facts</h2>
    <table>
      <tr><td>Serving size</td><td>30 g</td></tr>
      <tr><td>Energy</td><td>150 kcal</td></tr>
      <tr><td>Fat</td><td>8 g</td></tr>
      <tr><td>of which saturates</td><td>5 g</td></tr>
      <tr><td>Carbohydrate</td><td>1 g</td></tr>
      <tr><td>of which sugars</td><td>0.5 g</td></tr>
      <tr><td>Protein</td><td>19.5 g</td></tr>
      <tr><td>Calcium</td><td>0.6 g</td></tr>
      <tr><td>Salt</td><td>0.9 g</td></tr>
      <tr><td>Fibre</td><td>0 g</td></tr>
    </table>
  </section>
  <p class="storage">Store in a cool dry place</p>
  <address class="maker" style="font-style:normal">
    Manufactured &amp; distributed by:<br>Alpenkorn Snacks AG<br>Street: Bergstrasse 12<br>Address: 8000 Zurich<br>Tel: +41 44 555 01 20<br>info@alpenkorn-snacks.ch<br>www.alpenkorn-snacks.ch
  </address>
  <div class="web"><i></i><i></i><i></i><span>alpenkorn-snacks</span></div>
</main>
</body>
</html>
```